Candle Rental Business seeks new website design

We need a new website design for a Candle hire business. The business rents out pillar candles for events such as weddings and corporate events. Our main target market is weddings. The business name is Hire a Lantern. The business name does not have a logo design.

We would like a website that is light in colours and creates a warm atmosphere. The design needs to be elegant and upmarket. There are different size candles that we hire out, ranging from 10cm diameter to 20cm diameter, flat, tall etc. All our candles are white in colour. Its just the size that differs.

We would also like to include a section for hiring out decor such as glassvases, candlebras, overlays and chairs sachets, chair covers. However, this is not the businesses main focus but an additional offering to customers.

Target Market(s)

Wedding venues and brides. Corporate events. School dances.

Industry/Entity Type

Hospitality

Logo Text

Hire a Lantern

Number of Pages Required

1 page

Font styles to use
Sans Serif
Script

Requirements
Must have
• Pictures of pillar candles. Plain white candles. The website must centre around candles.
Nice to have
• Different examples of candle centrepieces
Should not have
• Pictures must not be of brides. Pictures of surrounding is perferable.

```html
<!DOCTYPE html>
<html lang="en">
<head>
<meta charset="utf-8">
<title>Hire a Lantern</title>
<link rel="stylesheet" href="https://fonts.googleapis.com/css2?family=Kaushan+Script&family=Roboto+Slab:wght@300;400&display=swap">
<style>
:root{
  --gold:#dfa92c;
  --rust:#c2531c;
  --ink:#4a4a4a;
  --muted:#7a7a7a;
  --cream:#f5f1e8;
  --olive:#97ad4f;
  --white:#ffffff;
}
*{margin:0;padding:0;box-sizing:border-box}
html,body{width:768px;height:1200px;overflow:hidden;background:var(--white)}
body{position:relative;font-family:"Roboto Slab",serif;color:var(--ink)}
.abs{position:absolute}
.hero{left:0;top:0;width:768px;height:349px;background:radial-gradient(ellipse at 20% 55%,#f1a08a 0%,#d9604f 22%,#7d5a3a 45%,#4d6a45 70%,#3f6240 100%)}
.nav{left:84px;top:0;width:600px;height:41px;background:var(--gold)}
.nav a{position:absolute;top:14px;font-size:10.5px;color:var(--white);text-decoration:none}
.brand{left:296px;top:0;width:160px;height:70px;background:var(--white);border-radius:0 0 80px 80px / 0 0 36px 36px;text-align:center;padding-top:15px;font-family:"Kaushan Script",cursive;font-size:21px;color:var(--rust)}
.tagline{left:0;top:155px;width:768px;text-align:center;font-family:"Kaushan Script",cursive;font-size:32px;color:var(--white)}
.thumb{top:287px;width:84px;height:44px;border:2px solid var(--white)}
.arrow{left:278px;top:280px;width:0;height:0;border-left:7px solid transparent;border-right:7px solid transparent;border-bottom:7px solid var(--white)}
h2{font-weight:400;font-size:16px;color:var(--ink)}
h2 span{color:var(--rust)}
.about-title{left:0;top:374px;width:768px;text-align:center}
.about-text{left:84px;top:407px;width:600px;text-align:center;font-weight:300;font-size:8.8px;line-height:15.6px;color:var(--muted)}
.band{left:0;top:484px;width:768px;height:338px;background:var(--cream)}
.card{background:var(--white)}
.card h3{position:absolute;font-weight:400;font-size:15.5px;color:var(--rust)}
.card p{position:absolute;font-weight:300;font-size:7.6px;line-height:13.2px;color:var(--muted)}
.btn{position:absolute;width:59px;height:17px;background:var(--olive);color:var(--white);font-size:7.5px;text-align:center;line-height:17px}
.gallery-title{left:84px;top:845px}
.photo{width:127px;height:71px}
.quote{left:524px;top:857px;width:160px;height:176px;background:var(--olive);color:var(--white);text-align:center}
.avatar{left:576px;top:844px;width:54px;height:54px;border-radius:50%;border:2px solid var(--white);background:radial-gradient(circle at 50% 40%,#d6b39a,#6b4a36)}
.quote p{position:absolute;left:10px;top:64px;width:140px;font-weight:300;font-size:7.6px;line-height:13.2px}
.quote strong{position:absolute;left:0;top:134px;width:160px;font-weight:400;font-size:9.5px}
.dot{top:1018px;height:2px;width:17px;background:rgba(255,255,255,.5)}
.footer{left:0;top:1057px;width:768px;height:143px;background:var(--gold);color:var(--white)}
.footer h4{position:absolute;font-weight:400;font-size:12px;color:var(--rust)}
.footer .small{position:absolute;font-size:8.8px;line-height:13.5px}
.social{top:1103px;width:19px;height:19px;border-radius:2px}
.rule{left:84px;top:1142px;width:600px;height:1px;background:rgba(255,255,255,.35)}
.links{left:0;top:1156px;width:768px;text-align:center;font-size:8.6px}
.links span{margin:0 5px}
.copy{left:0;top:1174px;width:768px;text-align:center;font-size:8.2px}
</style>
</head>
<body>

<section class="abs hero" role="img" aria-label="Close view of a lit red pillar candle beside a glass holder"></section>
<nav class="abs nav">
  <a style="left:37px">Home</a>
  <a style="left:98px">About Us</a>
  <a style="left:154px">Services</a>
  <a style="left:393px">Products</a>
  <a style="left:465px">Gallery</a>
  <a style="left:528px">Contact Us</a>
</nav>
<div class="abs brand">Hire a Lantern</div>
<div class="abs tagline">Meaningful gift at a friendly price point</div>
<div class="abs arrow"></div>
<div class="abs thumb" style="left:243px;background:linear-gradient(135deg,#7b8c5a,#d95a48 60%,#e8b9a0)" role="img" aria-label="Red candle slide"></div>
<div class="abs thumb" style="left:342px;background:linear-gradient(135deg,#3b2a20,#8a6a4e 50%,#c9c2b8)" role="img" aria-label="Dark candle slide"></div>
<div class="abs thumb" style="left:443px;background:linear-gradient(135deg,#b9c3e6,#e2d4ee 50%,#aab4de)" role="img" aria-label="Pastel candle slide"></div>

<h2 class="abs about-title">About <span>Hire a Lantern</span></h2>
<p class="abs about-text">We are a family owned and operated company and began making decorative candles for all occasions. All of our candles are individually hand made in our candle studio, situated in Kowhai Bay, outside Northvale. Our wax is local and of a very high quality, and dripless! Our wax is also made with a high melting point, which means it will not melt or bend in hot temperatures.</p>

<section class="abs band"></section>
<article class="abs card" style="left:84px;top:509px;width:225px;height:284px">
  <div class="abs" style="left:12px;top:10px;width:201px;height:120px;background:linear-gradient(160deg,#d8d4cc,#f4f2ee 45%,#8fb8c4)" role="img" aria-label="White pillar candles on a table with glassware"></div>
  <h3 style="left:12px;top:144px">Hire Candles</h3>
  <p style="left:12px;top:168px;width:203px">Do you love using candles for your events but tired of sorting old used candles or buying expensive candles. Believe it or not you can now rent candles. All our candles come in different sizes and heights. You can add the ambience of candlelight to your event of wedding ceremony without the worry over dripping wax or open candle flames.</p>
  <div class="btn" style="left:13px;top:266px">Read More</div>
</article>
<article class="abs card" style="left:321px;top:509px;width:363px;height:141px">
  <h3 style="left:12px;top:7px">Personalised Candles</h3>
  <p style="left:12px;top:36px;width:212px">Hire a Lantern provides the opportunity to give a thoughtful, meaningful gift at a friendly price point. This unique gift conveys the time and care you put into creating it. The recipient will enjoy the beautiful presentation and be reminded of the sentiment...</p>
  <div class="btn" style="left:12px;top:112px">Read More</div>
  <div class="abs" style="left:229px;top:10px;width:124px;height:124px;background:linear-gradient(160deg,#e4e5e8,#f6efe6 50%,#d7a9c0)" role="img" aria-label="Two personalised candles in glass jars"></div>
</article>
<article class="abs card" style="left:321px;top:663px;width:363px;height:141px">
  <h3 style="left:12px;top:7px">Décor Hire</h3>
  <p style="left:12px;top:36px;width:212px">We hire a selection of overlays, chair sachets and chair covers as well as glassware and candelabras to compliment your decor.</p>
  <div class="btn" style="left:12px;top:86px">Read More</div>
  <div class="abs" style="left:232px;top:11px;width:119px;height:119px;background:radial-gradient(circle at 50% 60%,#f1e6a8,#6d8a3e 45%,#5a2a22)" role="img" aria-label="Floral candle centrepiece on a dining table"></div>
</article>

<h2 class="abs gallery-title">Our <span>Photo Gallery</span></h2>
<div class="abs photo" style="left:84px;top:878px;background:linear-gradient(135deg,#7a4a2e,#e9dccc 55%,#8a9a6a)" role="img" aria-label="Candle display with flowers"></div>
<div class="abs photo" style="left:223px;top:878px;background:linear-gradient(135deg,#12345a,#3aa4d8 55%,#0e2a4a)" role="img" aria-label="Blue lit event table setting"></div>
<div class="abs photo" style="left:362px;top:878px;background:radial-gradient(circle at 45% 45%,#f2dca0,#7b5a28 50%,#2a1c0e)" role="img" aria-label="Glowing pillar candles"></div>
<div class="abs photo" style="left:84px;top:961px;background:radial-gradient(circle at 40% 55%,#e8c890,#6a3e1e 50%,#2a170b)" role="img" aria-label="Tall taper candles on a table"></div>
<div class="abs photo" style="left:223px;top:961px;background:radial-gradient(circle at 50% 60%,#e3b486,#7a4a2a 45%,#241408)" role="img" aria-label="Candlelit floral centrepieces"></div>
<div class="abs photo" style="left:362px;top:961px;background:linear-gradient(135deg,#3a2c22,#efe8e0 50%,#c8a888)" role="img" aria-label="Candle lighting at a ceremony"></div>

<aside class="abs quote">
  <p>"There are many variations of passages of Lorem Ipsum available, but the majority have suffered alteration in some form, by injected humour, or randomised words which don't look even slightly believable."</p>
  <strong>Marcus Ellery</strong>
</aside>
<div class="abs avatar" role="img" aria-label="Customer portrait"></div>
<div class="abs dot" style="left:575px;background:var(--white)"></div>
<div class="abs dot" style="left:595px"></div>
<div class="abs dot" style="left:615px"></div>

<footer class="abs footer">
  <h4 style="left:85px;top:22px">Location</h4>
  <div class="small" style="left:85px;top:43px">Simply dummy text printing<br>typesetting AT 12356</div>
  <div class="abs" style="left:0;top:27px;width:768px;text-align:center;font-size:12px;line-height:17px">+64 9 555 0142<br>hello@hirealantern.co</div>
  <h4 style="left:629px;top:22px">Follow us</h4>
</footer>
<div class="abs social" style="left:586px;background:#3b5998"></div>
<div class="abs social" style="left:612px;background:#2aa3ef"></div>
<div class="abs social" style="left:638px;background:#0a73b1"></div>
<div class="abs social" style="left:664px;background:#d6402e"></div>
<div class="abs rule"></div>
<div class="abs links" style="color:var(--white)">Home<span>I</span>About Us<span>I</span>Services<span>I</span>Products<span>I</span>Gallery<span>I</span>Contact Us</div>
<div class="abs copy" style="color:var(--white)">© 2016 Hire a Lantern, All Rights Reserved</div>

</body>
</html>
```